Luxury Wine Label for New Startup Winery

We need a wine label for our new winery startup. We have worked with a local designer but do not feel the resulting label / logo have the elevation required to present our brand as a luxury wine. Our winery is called "Quailbrook Vineyards" and we are focused on extremely high quality hand crafted artisan and estate wines from the Pacific Northwest.
We would like to see designs that utilize a tree line, or other imagery that represents the "Quailbrook" part of our company name. Another interesting feature could be wood grain.
A logo will be required based on your design so please design with this in mind:
This logo should be consistent with the wine bottle label design, and should be representative of our high end exclusive wine while giving a sense of place (Oregon/ Pacific Northwest.)
I will supply an image of the design we received from our local designer, PLEASE NOTE: in general we do like wood grain and tree line concepts but feel the execution was poorly done.
ATTN: Logo design should be suitable for use on: Bottles (Red wine/rose/white wine), Bussiness cards, vehicle signage, business signage, etc
P.S.:
If you have a design that is not outside the box we are still interested in seeing it.
Label is for a burgundy style bottle with a label height of 3.5 - 4" and a width of 3.5-4"
any label <= 4"x4" and >=3.5"x3.5" will be acceptable:
HOWEVER Width should be greater than or equal to height due to the bottle format
Target Market(s)
Wine enthusiasts with adequate discretionary budgets to afford $100 bottles of wine.
Industry/Entity Type
Wine / Winery
Requirements
Must have
- A sense of luxury, a feel of exclusivity, and a theme consistent with our product and brand name
Nice to have
- Tree line, wood grain or other wood themes. Serif fonts
Should not have
- anything cheesy, off topic, hard to read script fonts or anything that makes the label hard to read from a few feet away or too busy

```html
<!DOCTYPE html>
<html lang="en">
<head>
<meta charset="utf-8">
<title>Quailbrook Vineyards — Syrah Label</title>
<link rel="stylesheet" href="https://fonts.googleapis.com/css2?family=Cormorant+Garamond:wght@500&family=Allura&display=swap">
<style>
  :root {
    --backdrop: #0a0b0c;
    --label-charcoal: #2c2d2f;
    --label-charcoal-deep: #1f2022;
    --rule-silver: #a9abad;
    --ink-white: #eef0f2;
    --gold: #c89a5c;
    --gold-soft: #a88058;
    --wood-dark: #1d1a1a;
    --wood-mid: #4a2424;
    --wood-red: #7a3a36;
    --strip-black: #111214;
  }
  * { margin: 0; padding: 0; box-sizing: border-box; }
  html, body {
    width: 1200px; height: 1200px; overflow: hidden;
    background: var(--backdrop);
  }
  .canvas {
    position: relative; width: 1200px; height: 1200px;
    display: flex; align-items: center; justify-content: center;
  }
  .label {
    width: 1040px; height: 1000px;
    display: flex; flex-direction: column;
  }
  .label-main {
    position: relative; height: 640px;
    background: radial-gradient(ellipse at 50% 40%, var(--label-charcoal) 0%, var(--label-charcoal-deep) 100%);
  }
  .label-main .rule {
    position: absolute; left: 16px; right: 16px; height: 1px;
    background: var(--rule-silver); opacity: .75;
  }
  .label-main .rule.top { top: 36px; }
  .label-main .rule.bottom { bottom: 28px; }
  .brand {
    position: absolute; left: 0; right: 0; top: 230px;
    display: flex; flex-direction: column; align-items: center;
    font-family: "Cormorant Garamond", serif; font-weight: 500;
    color: var(--ink-white);
  }
  .brand-dot {
    width: 56px; height: 56px; border-radius: 50%;
    background: var(--ink-white); opacity: .9;
    margin-bottom: 64px;
  }
  .brand-name {
    font-size: 64px; letter-spacing: .42em; padding-left: .42em; line-height: 1;
  }
  .brand-sub {
    margin-top: 22px; font-size: 32px; letter-spacing: .42em; padding-left: .42em; line-height: 1;
  }
  .divider-strip {
    height: 14px; background: var(--strip-black);
    border-top: 1px solid #3a3b3e; border-bottom: 1px solid #3a3b3e;
  }
  .label-band {
    position: relative; height: 346px; overflow: hidden;
  }
  .wood-grain {
    position: absolute; inset: 0;
    background: linear-gradient(90deg, var(--wood-dark) 0%, var(--wood-dark) 25%, var(--wood-mid) 52%, var(--wood-red) 80%, var(--wood-mid) 100%);
  }
  .band-rule {
    position: absolute; left: 40px; right: 24px; top: 46px; height: 2px;
    background: linear-gradient(90deg, transparent, var(--gold) 12%, var(--gold) 88%, transparent);
  }
  .varietal {
    position: absolute; left: 0; right: 0; top: 110px; text-align: center;
    font-family: "Allura", cursive; font-size: 140px; line-height: 1;
    color: var(--gold);
  }
  .origin-line {
    position: absolute; left: 40px; right: 40px; bottom: 34px;
    display: flex; align-items: center; justify-content: center; gap: 20px;
    font-family: "Cormorant Garamond", serif; font-weight: 500;
    font-size: 32px; letter-spacing: .04em; line-height: 1; color: var(--gold-soft);
  }
  .origin-line .lead-rule { width: 60px; height: 2px; background: var(--gold); }
  .origin-line .sep { width: 1px; height: 42px; background: var(--gold-soft); }
  .origin-line .year { color: var(--gold); opacity: .7; }
</style>
</head>
<body>
<main class="canvas">
  <article class="label">
    <section class="label-main">
      <div class="rule top"></div>
      <div class="brand">
        <span class="brand-dot" aria-hidden="true"></span>
        <div class="brand-name">QUAILBROOK</div>
        <div class="brand-sub">VINEYARDS</div>
      </div>
      <div class="rule bottom"></div>
    </section>
    <div class="divider-strip"></div>
    <section class="label-band">
      <div class="wood-grain" role="img" aria-label="Dark red-stained wood grain texture"></div>
      <div class="band-rule"></div>
      <div class="varietal">Syrah</div>
      <div class="origin-line">
        <span class="lead-rule"></span>
        <span>PACIFIC</span>
        <span class="sep"></span>
        <span class="year">2025</span>
        <span class="sep"></span>
        <span>NORTHWEST</span>
      </div>
    </section>
  </article>
</main>
</body>
</html>
```